Business Card Update, need to bring life to the card, two sided color

We need a new business card design, are moving and changing addresses and need a new look, we have the logos already attached but need a new style moving forward. Can incorporate the color of the logo (The Green) as well, maybe a solid back? We deal with safety products revolving around static electricity and safety lighting. Would like to keep same font in second logo as well.

Target Market(s)

Electrical Safety, Lighting

Contact Information for Business Card

Dale Fenwick
Vice President
Office: 770-555-4821
Cell: 770-555-3067
dale@tkfenwick.example
www.tkfenwick.example
4700 West Harbor Boulevard
Suite #150
Roswell, GA 30076

Font styles to use
Serif
Sans Serif

Requirements
Must have
• Since 1918
Nice to have
• Could use the 100 Year Logo for back of card, would like the back of card to be the same green as logo.
Should not have
• No black cards please.

```html
<!DOCTYPE html>
<html lang="en">
<head>
<meta charset="utf-8">
<title>T.K. Fenwick — Business Card</title>
<link href="https://fonts.googleapis.com/css2?family=Source+Sans+3:wght@400;600;700&display=swap" rel="stylesheet">
<style>
  :root {
    --backdrop: #141414;
    --green: #0f9a63;
    --green-deep: #0b7f51;
    --paper: #f5f6f3;
    --paper-edge: #dcded9;
    --ink: #2b2d2c;
    --ink-soft: #5b5e5c;
    --on-green: #ffffff;
    --on-green-soft: #d7f0e4;
    --rule: #c9ccc7;
  }
  * { margin: 0; padding: 0; box-sizing: border-box; }
  html, body { width: 1200px; height: 900px; overflow: hidden; }
  body {
    background: var(--backdrop);
    font-family: "Source Sans 3", "Myriad Pro", Arial, sans-serif;
    position: relative;
  }
  .card {
    position: absolute;
    left: 320px;
    width: 560px;
    height: 320px;
    border-radius: 22px;
    box-shadow: 0 14px 30px rgba(0,0,0,.55);
  }
  .card--back { top: 110px; background: var(--green); border: 1px solid var(--green-deep); }
  .card--front { top: 470px; background: var(--paper); border: 1px solid var(--paper-edge); }

  /* back side */
  .back-mark {
    position: absolute;
    top: 100px; left: 0; right: 0;
    display: flex; align-items: center; justify-content: center; gap: 14px;
  }
  .back-mark__dot {
    width: 58px; height: 58px; border-radius: 50%;
    background: var(--on-green);
  }
  .back-mark__name {
    font-size: 30px; font-weight: 700; color: var(--on-green);
  }
  .back-since {
    position: absolute;
    top: 176px; left: 0; right: 0;
    text-align: center;
    font-size: 14px; font-weight: 600; letter-spacing: 3px;
    text-transform: uppercase; color: var(--on-green-soft);
  }
  .back-url {
    position: absolute;
    left: 0; right: 0; bottom: 40px;
    text-align: center;
    font-size: 15px; color: var(--on-green); letter-spacing: .2px;
  }

  /* front side */
  .front-mark {
    position: absolute;
    top: 42px; left: 180px;
    display: flex; align-items: center; gap: 12px;
  }
  .front-mark__dot {
    width: 46px; height: 46px; border-radius: 50%;
    background: var(--green);
  }
  .front-mark__text { color: var(--green); font-weight: 700; line-height: 1.05; }
  .front-mark__name { font-size: 27px; }
  .front-mark__sub { font-size: 14px; }
  .front-rule {
    position: absolute;
    left: 176px; right: 34px; top: 124px;
    height: 1px; background: var(--rule);
  }
  .person {
    position: absolute; left: 34px; top: 146px;
  }
  .person__name {
    font-size: 24px; font-weight: 600; color: var(--green);
    text-transform: uppercase; letter-spacing: -.2px; line-height: 1;
  }
  .person__title { font-size: 17px; color: var(--ink-soft); margin-top: 3px; }
  .contact {
    position: absolute; left: 34px; top: 218px;
    list-style: none;
  }
  .contact li {
    display: flex; align-items: center; gap: 8px;
    font-size: 17px; color: var(--ink); line-height: 24px;
  }
  .contact svg { width: 14px; height: 14px; fill: var(--green); flex: none; }
  .address {
    position: absolute; right: 34px; top: 146px;
    text-align: right; font-size: 16px; color: var(--ink); line-height: 22px;
    font-style: normal;
  }
</style>
</head>
<body>

<section class="card card--back" aria-label="Card back">
  <div class="back-mark">
    <span class="back-mark__dot"></span>
    <span class="back-mark__name">T.K. Fenwick</span>
  </div>
  <p class="back-since">Since 1918</p>
  <p class="back-url">www.tkfenwick.example</p>
</section>

<section class="card card--front" aria-label="Card front">
  <div class="front-mark">
    <span class="front-mark__dot"></span>
    <div class="front-mark__text">
      <div class="front-mark__name">T.K. Fenwick</div>
      <div class="front-mark__sub">Manufacturing Company, Inc.</div>
    </div>
  </div>
  <div class="front-rule"></div>

  <div class="person">
    <h1 class="person__name">Dale Fenwick</h1>
    <p class="person__title">Vice President</p>
  </div>

  <ul class="contact">
    <li>
      <svg viewBox="0 0 16 16" aria-hidden="true"><path d="M3.6 1.5l2.3 2.6-1.3 1.6c.9 2 2.6 3.7 4.7 4.7l1.6-1.3 2.6 2.3-1.2 2.1C6.8 13.3 2.7 9.2 1.5 3.7z"/></svg>
      770-555-4821
    </li>
    <li>
      <svg viewBox="0 0 16 16" aria-hidden="true"><path d="M4.5 0h7a1 1 0 0 1 1 1v14a1 1 0 0 1-1 1h-7a1 1 0 0 1-1-1V1a1 1 0 0 1 1-1zm.6 2v10.5h5.8V2zM8 13.3a.9.9 0 1 0 0 1.8.9.9 0 0 0 0-1.8z"/></svg>
      770-555-3067
    </li>
    <li>
      <svg viewBox="0 0 16 16" aria-hidden="true"><path d="M1 3h14v1.2L8 9 1 4.2zm0 2.6l7 4.8 7-4.8V13H1z"/></svg>
      dale@tkfenwick.example
    </li>
  </ul>

  <address class="address">
    4700 West Harbor Boulevard<br>
    Suite #150<br>
    Roswell, GA 30076
  </address>
</section>

</body>
</html>
```